Website Design for a holiday home letting busines

We require a redesign of our present website www.pinebrookstays.com. We want the website to stand out and look professional and clean to make holiday hunters want to book a caravan or lodge holiday with us. Our logo is red however we DO NOT want the website to be red. We want a natural colour scheme.

The final design should communicate that we are a professional company to book with.

On the home page we require;
Overview of company
Photo
Search box for holiday (check in)
Late Deals
Reviews
News

We would like the following pages designed; home page, available dates page, caravans page, content page.

The website should be responsive for smart phones. One website I do like is http://www.verdoliso.be/nl/

Target Market(s)

Families

Industry/Entity Type

Travel

Number of Pages Required

5+ page

Font styles to use
Serif

Requirements
Must have
• The project must be responsive for mobile phones and tablets.
• Ability to search for holiday home holidays
• We want a natural colour scheme.
Nice to have
• A style we like is http://www.verdoliso.be/nl/
Should not have
• Do not use red as a colour for the website. Our logo is red so this is the only time we want this used.

```html
<!DOCTYPE html>
<html lang="en">
<head>
<meta charset="utf-8">
<title>Pinebrook Stays – Caravan &amp; Lodge Holidays</title>
<link href="https://fonts.googleapis.com/css2?family=Open+Sans:wght@400;600;700;800&display=swap" rel="stylesheet">
<style>
:root{
  --blue:#2f86c8;
  --blue-dark:#1f6aa5;
  --navy:#1e3a50;
  --navy-deep:#162b3c;
  --footer:#26333e;
  --footer-deep:#1b252d;
  --ink:#2d3a44;
  --muted:#7b8893;
  --line:#dfe5ea;
  --pale:#eef3f6;
  --star:#f0b62b;
  --logo-red:#c8242b;
  --white:#ffffff;
}
*{box-sizing:border-box;margin:0;padding:0}
html,body{width:1200px;height:2576px;overflow:hidden}
body{font-family:"Open Sans",Arial,sans-serif;color:var(--ink);background:var(--white);font-size:13px;line-height:1.5;position:relative}
.abs{position:absolute}
.btn{display:inline-block;background:var(--blue);color:var(--white);font-size:11px;font-weight:600;padding:5px 12px;border-radius:2px}
.btn.light{background:#dfeaf3;color:var(--blue-dark)}
.section-title{text-align:center;font-size:24px;font-weight:700;letter-spacing:.5px;text-transform:uppercase}
.section-intro{text-align:center;font-size:12px;color:var(--muted);width:560px;margin:8px auto 0}
.photo{background:linear-gradient(135deg,#c9b79c,#8a6f55)}
.photo.room{background:linear-gradient(135deg,#d9c7ae,#9b7c5c)}
.photo.sea{background:linear-gradient(180deg,#7cc3e6,#3c9bc9 60%,#d9ccb0)}
.photo.bed{background:linear-gradient(135deg,#e8ddcc,#b49a7a)}
.arrow{width:30px;height:30px;border-radius:50%;background:#e6ebef;display:flex;align-items:center;justify-content:center}

/* top bar */
.topbar{left:0;top:0;width:1200px;height:40px;display:flex;align-items:center;padding:0 40px;justify-content:space-between}
.brand{display:flex;align-items:center;gap:8px;font-size:18px;font-weight:700;color:var(--ink)}
.brand-dot{width:22px;height:22px;border-radius:50%;background:var(--logo-red)}
.contact-line{display:flex;gap:22px;align-items:center;font-size:11px;color:var(--muted)}
.contact-line span{display:flex;align-items:center;gap:6px}
.social-square{width:20px;height:20px;background:#3b5b98;border-radius:3px}

/* nav */
.mainnav{left:0;top:40px;width:1200px;height:30px;background:var(--blue);display:flex;justify-content:center}
.mainnav a{color:var(--white);font-size:10.5px;font-weight:600;text-decoration:none;padding:0 17px;line-height:30px;text-transform:uppercase}
.mainnav a.active{background:var(--blue-dark)}

/* hero */
.hero{left:0;top:70px;width:1200px;height:362px;background:linear-gradient(180deg,#a9d8f1 0%,#d7eefa 45%,#f1ead9 75%,#e6d8bb 100%)}
.hero-title{left:40px;top:70px;color:var(--white);font-size:46px;font-weight:800;line-height:1.1;text-transform:uppercase;text-shadow:0 2px 6px rgba(0,0,0,.25)}
.book-now{left:1112px;top:76px;width:58px;height:50px;background:var(--blue);color:var(--white);font-size:10px;font-weight:700;text-align:center;padding-top:12px;line-height:1.2}
.hero .arrow{position:absolute;top:165px;background:rgba(255,255,255,.85)}

/* popup */
.popup{left:250px;top:60px;width:700px;height:340px;border:6px solid var(--white);box-shadow:0 6px 30px rgba(0,0,0,.35)}
.popup-photo{position:absolute;inset:0;background:linear-gradient(180deg,#5fb6e3 0%,#8fd0ef 40%,#e9dcbd 75%,#d8c49f 100%)}
.popup-title{position:absolute;top:28px;width:100%;text-align:center;color:var(--white);font-size:30px;font-weight:800;letter-spacing:1px;text-shadow:0 2px 5px rgba(0,0,0,.3)}
.popup-form{position:absolute;left:140px;top:86px;display:flex;gap:6px}
.popup-form .field{width:260px;height:30px;background:var(--white);border-radius:2px;font-size:11px;color:var(--muted);padding:6px 10px}
.popup-form .btn{height:30px;line-height:20px;padding:5px 18px}
.popup-close{left:930px;top:42px;width:28px;height:28px;border-radius:50%;background:var(--white);box-shadow:0 1px 4px rgba(0,0,0,.3);display:flex;align-items:center;justify-content:center}

/* search */
.search{left:0;top:432px;width:1200px;height:80px;background:var(--pale);display:flex;align-items:center;padding:0 40px;gap:18px}
.search-label{font-size:15px;font-weight:700;line-height:1.15;text-transform:uppercase;width:140px}
.search-label small{display:block;font-size:11px;color:var(--muted);font-weight:600}
.search-group{display:flex;align-items:center;gap:8px;font-size:11px;color:var(--muted)}
.search-input{width:160px;height:30px;background:var(--white);border:1px solid var(--line);font-size:11px;padding:6px 9px;color:var(--ink);display:flex;justify-content:space-between}
.search .btn{height:32px;line-height:22px;padding:5px 20px;font-size:11px}

/* late deals */
.deals{left:0;top:530px;width:1200px;height:420px}
.deals .section-title{margin-top:8px}
.card-row{position:absolute;left:90px;top:110px;display:flex;gap:20px}
.deal-card{width:240px;background:var(--white);border:1px solid var(--line)}
.deal-card .photo{height:140px}
.card-body{padding:10px 12px}
.card-body h4{font-size:12px;font-weight:700}
.card-body p{font-size:11px;color:var(--muted)}
.card-actions{display:flex;gap:6px;margin-top:8px}
.deals .arrow{position:absolute;top:215px}
.dots{position:absolute;top:362px;width:100%;display:flex;justify-content:center;gap:6px}
.dots i{width:8px;height:8px;border-radius:50%;background:var(--line)}
.dots i.on{background:var(--blue)}

/* overview + reviews */
.overview{left:40px;top:968px;width:560px}
.col-title{font-size:20px;font-weight:700;text-transform:uppercase;padding-bottom:8px;border-bottom:2px solid var(--line);position:relative}
.col-title:after{content:"";position:absolute;left:0;bottom:-2px;width:60px;height:2px;background:var(--blue)}
.overview-body{display:flex;gap:18px;margin-top:18px}
.overview-body .photo{width:240px;height:200px;flex:none}
.overview-body p{font-size:12px;color:var(--muted);margin-bottom:10px}
.overview-body p.lead{color:var(--blue-dark);font-weight:600}
.reviews{left:640px;top:968px;width:520px}
.review{margin-top:18px;padding-bottom:16px;border-bottom:1px solid var(--line)}
.review h5{font-size:12px;color:var(--blue-dark);font-weight:600}
.review p{font-size:12px;color:var(--muted)}
.stars{display:flex;gap:3px;margin-top:6px}

/* caravans */
.caravans{left:0;top:1340px;width:1200px;height:560px;background:linear-gradient(180deg,var(--navy),var(--navy-deep))}
.caravans .section-title{color:var(--white);margin-top:56px}
.caravans .section-intro{color:#a9bccb}
.caravans .card-row{top:170px;left:110px}
.lodge-card{width:230px;background:var(--white)}
.lodge-card .photo{height:170px}
.caravans .arrow{position:absolute;top:300px;background:rgba(255,255,255,.15)}

/* blog + feed */
.blog{left:40px;top:1930px;width:720px}
.blog-row{display:flex;gap:20px;margin-top:18px}
.blog-card{width:200px}
.blog-card .photo{height:130px;position:relative}
.date-tag{position:absolute;left:0;bottom:0;background:var(--blue);color:var(--white);font-size:10px;font-weight:600;padding:3px 8px}
.blog-card h4{font-size:12px;font-weight:700;color:var(--blue-dark);margin-top:8px}
.blog-card p{font-size:11px;color:var(--muted)}
.feed{left:800px;top:1930px;width:360px}
.feed-item{display:flex;gap:12px;margin-top:18px}
.feed-item .photo{width:70px;height:60px;flex:none}
.feed-item h5{font-size:12px;color:var(--blue-dark);font-weight:600}
.feed-item p{font-size:11px;color:var(--muted)}
.live-chat{left:1068px;top:2196px;width:132px;height:48px;background:var(--blue);color:var(--white);font-size:11px;font-weight:700;display:flex;align-items:center;padding-left:14px;gap:10px}
.live-chat .photo{width:40px;height:48px;background:linear-gradient(135deg,#e2c6ad,#8e6a4f)}

/* footer */
.footer{left:0;top:2268px;width:1200px;height:262px;background:var(--footer);color:#b7c3cc;padding:30px 40px;display:flex;gap:40px}
.footer h6{color:var(--white);font-size:13px;font-weight:700;text-transform:uppercase;margin-bottom:14px}
.footer li{list-style:none;font-size:11px;margin-bottom:7px;display:flex;gap:8px;align-items:flex-start}
.foot-contact{width:300px}
.foot-news{width:300px}
.foot-news .field{height:28px;background:#33424e;border:1px solid #40505c;margin-bottom:8px;font-size:11px;padding:5px 9px;color:#8c9aa5}
.foot-links{display:flex;gap:60px}
.foot-links ul{width:150px}
.bottom-bar{left:0;top:2530px;width:1200px;height:46px;background:var(--footer-deep);color:#7f8d98;font-size:11px;display:flex;align-items:center;justify-content:space-between;padding:0 40px}
.social-dots{display:flex;gap:8px}
.social-dots i{width:24px;height:24px;border-radius:50%;border:1px solid #55646f}
</style>
</head>
<body>

<header class="abs topbar">
  <div class="brand"><span class="brand-dot"></span>Pinebrook Stays</div>
  <div class="contact-line">
    <span><svg width="14" height="10" viewBox="0 0 14 10"><rect x=".5" y=".5" width="13" height="9" fill="none" stroke="#7b8893"/><path d="M.5 .5 7 6 13.5 .5" fill="none" stroke="#7b8893"/></svg>info@pinebrookstays.com</span>
    <span><svg width="12" height="12" viewBox="0 0 12 12"><path d="M2 1h3l1 3-2 1a7 7 0 0 0 3 3l1-2 3 1v3c-6 1-10-3-9-9z" fill="#7b8893"/></svg>01234 567 890</span>
    <span class="social-square"></span>
  </div>
</header>

<nav class="abs mainnav">
  <a class="active">Home</a><a>About</a><a>Reviews</a><a>Caravans &amp; Lodges</a><a>Gallery</a><a>Special Offers</a><a>Available Dates</a><a>Local Attractions</a><a>Contact</a>
</nav>

<section class="abs hero" role="img" aria-label="Photo of a sunny beach with deckchairs under a blue sky">
  <div class="abs hero-title">Private<br>Holiday<br>Rentals</div>
  <div class="abs book-now">BOOK<br>NOW</div>
  <span class="arrow" style="left:20px"><svg width="10" height="12" viewBox="0 0 10 12"><path d="M7 1 2 6l5 5" stroke="#2d3a44" stroke-width="2" fill="none"/></svg></span>
  <span class="arrow" style="left:1150px"><svg width="10" height="12" viewBox="0 0 10 12"><path d="M3 1l5 5-5 5" stroke="#2d3a44" stroke-width="2" fill="none"/></svg></span>
</section>

<div class="abs popup">
  <div class="popup-photo" role="img" aria-label="Photo of a couple relaxing on a sandy beach by the sea"></div>
  <div class="popup-title">SUBSCRIBE TO MAILPOST</div>
  <div class="popup-form"><div class="field">Enter your email address</div><span class="btn">SUBSCRIBE</span></div>
</div>
<div class="abs popup-close"><svg width="10" height="10" viewBox="0 0 10 10"><path d="M1 1l8 8M9 1 1 9" stroke="#2d3a44" stroke-width="2"/></svg></div>

<section class="abs search">
  <div class="search-label">Search Box<small>For Holiday</small></div>
  <div class="search-group">Check in date <div class="search-input">28/09/2015 <svg width="12" height="12" viewBox="0 0 12 12"><rect x="1" y="2" width="10" height="9" fill="none" stroke="#7b8893"/><path d="M1 5h10" stroke="#7b8893"/></svg></div></div>
  <div class="search-group">Number of nights <div class="search-input">7 nights <span>▾</span></div></div>
  <div class="search-group">Guests <div class="search-input" style="width:110px">2 adults <span>▾</span></div></div>
  <span class="btn">SEARCH NOW</span>
</section>

<section class="abs deals">
  <h2 class="section-title">Late Deals</h2>
  <p class="section-intro">Grab a last minute break at one of our lodges or caravans. Short stays and weekly bookings at reduced prices, available now.</p>
  <span class="arrow" style="left:40px"><svg width="10" height="12" viewBox="0 0 10 12"><path d="M7 1 2 6l5 5" stroke="#7b8893" stroke-width="2" fill="none"/></svg></span>
  <span class="arrow" style="left:1130px"><svg width="10" height="12" viewBox="0 0 10 12"><path d="M3 1l5 5-5 5" stroke="#7b8893" stroke-width="2" fill="none"/></svg></span>
  <div class="card-row">
    <div class="deal-card"><div class="photo room" role="img" aria-label="Photo of a lodge living room"></div><div class="card-body"><h4>The Dunes</h4><p>Friday 4th September 2015</p><p>3 nights from £189</p><div class="card-actions"><span class="btn light">Price £189</span><span class="btn">Book now</span></div></div></div>
    <div class="deal-card"><div class="photo bed" role="img" aria-label="Photo of a caravan bedroom"></div><div class="card-body"><h4>The Willows</h4><p>Friday 4th September 2015</p><p>4 nights from £225</p><div class="card-actions"><span class="btn light">Price £225</span><span class="btn">Book now</span></div></div></div>
    <div class="deal-card"><div class="photo" role="img" aria-label="Photo of a lodge bedroom with wooden furniture"></div><div class="card-body"><h4>Heron Lodge</h4><p>Friday 4th September 2015</p><p>7 nights from £349</p><div class="card-actions"><span class="btn light">Price £349</span><span class="btn">Book now</span></div></div></div>
    <div class="deal-card"><div class="photo sea" role="img" aria-label="Photo of a pool beside the sea"></div><div class="card-body"><h4>Seaview Park</h4><p>Friday 4th September 2015</p><p>3 nights from £199</p><div class="card-actions"><span class="btn light">Price £199</span><span class="btn">Book now</span></div></div></div>
  </div>
  <div class="dots"><i class="on"></i><i></i><i></i></div>
</section>

<section class="abs overview">
  <h3 class="col-title">Overview of Company</h3>
  <div class="overview-body">
    <div class="photo room" role="img" aria-label="Photo of a bright lodge interior"></div>
    <div>
      <p class="lead">A family run business offering comfortable caravans and lodges in quiet, green surroundings.</p>
      <p>We have welcomed families for many years and take pride in clean, well kept homes, friendly service and easy booking from start to finish.</p>
      <p>Every lodge is close to walks, beaches and local attractions, so there is something for everyone.</p>
      <span class="btn">Read more</span>
    </div>
  </div>
</section>

<section class="abs reviews">
  <h3 class="col-title">Latest Reviews</h3>
  <div class="review"><h5>A wonderful week away</h5><p>The lodge was spotless and the children loved the park. We will certainly be booking again next summer.</p>
    <div class="stars"><svg width="80" height="14" viewBox="0 0 80 14"><g fill="#f0b62b"><path id="s" d="M7 0l2 5h5l-4 3 2 5-5-3-5 3 2-5-4-3h5z"/><use href="#s" x="16"/><use href="#s" x="32"/><use href="#s" x="48"/><use href="#s" x="64"/></g></svg></div></div>
  <div class="review"><h5>Relaxing and great value</h5><p>Lovely quiet setting with everything we needed. Friendly owners and a very easy check in.</p>
    <div class="stars"><svg width="80" height="14" viewBox="0 0 80 14"><g fill="#f0b62b"><use href="#s"/><use href="#s" x="16"/><use href="#s" x="32"/><use href="#s" x="48"/><use href="#s" x="64"/></g></svg></div></div>
</section>

<section class="abs caravans">
  <h2 class="section-title">List of Caravans and Lodges</h2>
  <p class="section-intro">Choose from our range of caravans and lodges, each fully equipped for a relaxing family holiday.</p>
  <span class="arrow" style="left:40px"><svg width="10" height="12" viewBox="0 0 10 12"><path d="M7 1 2 6l5 5" stroke="#fff" stroke-width="2" fill="none"/></svg></span>
  <span class="arrow" style="left:1130px"><svg width="10" height="12" viewBox="0 0 10 12"><path d="M3 1l5 5-5 5" stroke="#fff" stroke-width="2" fill="none"/></svg></span>
  <div class="card-row">
    <div class="lodge-card"><div class="photo bed" role="img" aria-label="Photo of a lodge bedroom"></div><div class="card-body"><h4>The Dunes</h4><p>Sleeps 6 · 3 bedrooms</p><div class="card-actions"><span class="btn light">Details</span><span class="btn">Book now</span></div></div></div>
    <div class="lodge-card"><div class="photo room" role="img" aria-label="Photo of a caravan lounge"></div><div class="card-body"><h4>The Willows</h4><p>Sleeps 4 · 2 bedrooms</p><div class="card-actions"><span class="btn light">Details</span><span class="btn">Book now</span></div></div></div>
    <div class="lodge-card"><div class="photo" role="img" aria-label="Photo of a lodge kitchen"></div><div class="card-body"><h4>Heron Lodge</h4><p>Sleeps 6 · 3 bedrooms</p><div class="card-actions"><span class="btn light">Details</span><span class="btn">Book now</span></div></div></div>
    <div class="lodge-card"><div class="photo bed" role="img" aria-label="Photo of a twin bedroom"></div><div class="card-body"><h4>Seaview Park</h4><p>Sleeps 4 · 2 bedrooms</p><div class="card-actions"><span class="btn light">Details</span><span class="btn">Book now</span></div></div></div>
  </div>
</section>

<section class="abs blog">
  <h3 class="col-title">Latest Blog News</h3>
  <div class="blog-row">
    <div class="blog-card"><div class="photo room" role="img" aria-label="Photo of a lodge interior"><span class="date-tag">August 20, 2015</span></div><h4>New lodges open for 2016</h4><p>Three new lodges are ready to book for next season.</p></div>
    <div class="blog-card"><div class="photo bed" role="img" aria-label="Photo of a bedroom"><span class="date-tag">August 12, 2015</span></div><h4>Autumn breaks now open</h4><p>Enjoy quiet walks and cosy nights this autumn.</p></div>
    <div class="blog-card"><div class="photo" role="img" aria-label="Photo of a lounge"><span class="date-tag">August 03, 2015</span></div><h4>Things to do nearby</h4><p>Our guide to beaches, parks and days out.</p></div>
  </div>
</section>

<section class="abs feed">
  <h3 class="col-title">Community Feed</h3>
  <div class="feed-item"><div class="photo bed" role="img" aria-label="Photo of a lodge bedroom"></div><div><h5>Pinebrook Stays</h5><p>Late availability this weekend in two of our lodges. Call us today.</p></div></div>
  <div class="feed-item"><div class="photo room" role="img" aria-label="Photo of a caravan lounge"></div><div><h5>Pinebrook Stays</h5><p>Thank you to all our guests for another lovely summer season.</p></div></div>
</section>

<div class="abs live-chat">LIVE CHAT<div class="photo" role="img" aria-label="Photo of a support assistant"></div></div>

<footer class="abs footer">
  <div class="foot-contact">
    <h6>Contact Us</h6>
    <ul>
      <li><svg width="12" height="12" viewBox="0 0 12 12"><path d="M2 1h3l1 3-2 1a7 7 0 0 0 3 3l1-2 3 1v3c-6 1-10-3-9-9z" fill="#b7c3cc"/></svg>Telephone: 01234 567 890</li>
      <li><svg width="12" height="10" viewBox="0 0 14 10"><rect x=".5" y=".5" width="13" height="9" fill="none" stroke="#b7c3cc"/><path d="M.5 .5 7 6 13.5 .5" fill="none" stroke="#b7c3cc"/></svg>Email: info@pinebrookstays.com</li>
      <li><svg width="12" height="14" viewBox="0 0 12 14"><path d="M6 0a5 5 0 0 1 5 5c0 4-5 9-5 9S1 9 1 5a5 5 0 0 1 5-5z" fill="#b7c3cc"/><circle cx="6" cy="5" r="2" fill="#26333e"/></svg>Pinebrook Stays, Holly Lane,<br>Fernside Park, Northshire NS4 2PB</li>
    </ul>
  </div>
  <div class="foot-news">
    <h6>Newsletter Signup</h6>
    <div class="field">Your name</div>
    <div class="field">Your email address</div>
    <span class="btn">SUBMIT</span>
  </div>
  <div>
    <h6>Company Links</h6>
    <div class="foot-links">
      <ul><li>About Us</li><li>Reviews</li><li>Caravans &amp; Lodges</li><li>Gallery</li><li>Special Offers</li><li>Contact</li></ul>
      <ul><li>Available Dates</li><li>Local Attractions</li><li>Booking Terms</li><li>Privacy Policy</li><li>FAQs</li><li>Blog</li></ul>
    </div>
  </div>
</footer>
<div class="abs bottom-bar">
  <span>© 2015 Copyright · www.pinebrookstays.com · All rights reserved</span>
  <div class="social-dots"><i></i><i></i><i></i><i></i></div>
</div>

</body>
</html>
```